New Business Card Design Project LORVANTI-Italy

we are LORVANTI-Italy
our company in the market for 3 years we are luxury cosmetic company and its about time for a facelift :)
i will like to have elegant luxurious and unique business card
that will give the person that get it a unique, luxurious and elegant impression
I'm VERY OPEN FOR NEW IDEAS , even duo i add a few files of things that i see on line and i like them

i add my logo as well
my website is LORVANTI.COM
(if you would like to see the main style that we have)

Target Market(s)

adult that have money :)

Industry/Entity Type

Business

Contact Information for Business Card

Name - Dario Lorvanti
Position - CEO and CO Founder
address - 4817 E Halvern
telephone - 555-384-1926
email - dario@lorvanti.com
fax - 555-384-1926
website - LORVANTI.COM

Colors
000000
959595
fbee3e
ffffff

Requirements
Must have
• big logo in GOLD color
• elegant look
• impressive
Nice to have
• not must but maybe classy pattern background
• not must but maybe emblem
• maybe clear plastic business card
Should not have
• colors
• images

```html
<!DOCTYPE html>
<html lang="en">
<head>
<meta charset="utf-8">
<title>LORVANTI Italy – Business Card</title>
<link rel="stylesheet" href="https://fonts.googleapis.com/css2?family=Cinzel:wght@500&family=Open+Sans:wght@400;600;700&display=swap">
<style>
  :root {
    --stage: #2b2a29;
    --card-black: #0d0d0d;
    --gold: #d9b54c;
    --gold-band: #dcbe57;
    --grey: #959595;
    --white: #ffffff;
    --ink: #111111;
  }
  * { box-sizing: border-box; margin: 0; padding: 0; }
  html, body {
    width: 1200px; height: 716px; overflow: hidden;
    background: var(--stage);
  }
  .stage {
    position: relative; width: 1200px; height: 716px;
  }
  .card {
    position: absolute; top: 208px;
    width: 520px; height: 300px;
    background: var(--card-black);
    overflow: hidden;
    box-shadow: 0 14px 30px rgba(0,0,0,.55);
  }
  .card--front { left: 50px; }
  .card--back  { left: 630px; }

  /* brand block */
  .brand {
    position: absolute; display: flex; flex-direction: column; align-items: center;
    color: var(--gold);
    font-family: "Cinzel", serif; font-weight: 500;
  }
  .brand__disc {
    border-radius: 50%; border: 2px solid var(--gold);
  }
  .brand__name { line-height: 1; letter-spacing: 1px; }
  .brand__rule { height: 2px; background: var(--gold); }
  .brand__place { letter-spacing: 2px; line-height: 1; }

  .card--front .brand { left: 0; right: 0; top: 62px; }
  .card--front .brand__disc { width: 72px; height: 72px; margin-bottom: 12px; }
  .card--front .brand__name { font-size: 50px; }
  .card--front .brand__rule { width: 300px; margin: 10px 0 8px; }
  .card--front .brand__place { font-size: 16px; }

  .card--back .brand { left: 190px; width: 260px; top: 24px; }
  .card--back .brand__disc { width: 62px; height: 62px; margin-bottom: 8px; }
  .card--back .brand__name { font-size: 38px; }
  .card--back .brand__rule { width: 220px; margin: 8px 0 6px; }
  .card--back .brand__place { font-size: 13px; }

  /* person */
  .person {
    position: absolute; left: 24px; top: 160px;
    font-family: "Open Sans", sans-serif; color: var(--white);
  }
  .person__name { font-size: 15px; font-weight: 700; }
  .person__role { font-size: 8px; color: #cfcfcf; margin-top: 1px; }
  .person-rule {
    position: absolute; left: 24px; top: 196px; width: 220px; height: 1px;
    background: var(--gold);
  }

  .bands { position: absolute; left: 0; top: 0; width: 520px; height: 300px; }

  .contact {
    position: absolute; list-style: none;
    font-family: "Open Sans", sans-serif; font-weight: 600; color: var(--ink);
  }
  .contact li { display: flex; align-items: center; gap: 8px; height: 19px; font-size: 13px; }
  .contact svg { width: 11px; height: 11px; fill: var(--ink); flex: none; }
  .contact--personal { left: 24px; top: 208px; }
  .contact--office { left: 346px; top: 222px; }
  .contact--address { left: 352px; top: 279px; }
  .contact--address li { font-size: 14px; font-weight: 700; }
</style>
</head>
<body>
<main class="stage">

  <section class="card card--front" aria-label="Card front">
    <div class="brand">
      <div class="brand__disc"></div>
      <div class="brand__name">LORVANTI</div>
      <div class="brand__rule"></div>
      <div class="brand__place">ITALY</div>
    </div>
  </section>

  <section class="card card--back" aria-label="Card back">
    <svg class="bands" viewBox="0 0 520 300" aria-hidden="true">
      <rect x="0" y="200" width="520" height="100" fill="var(--gold-band)"/>
      <rect x="0" y="284" width="520" height="16" fill="var(--grey)"/>
      <polygon points="330,300 344,270 520,270 520,300" fill="var(--grey)"/>
    </svg>

    <div class="brand">
      <div class="brand__disc"></div>
      <div class="brand__name">LORVANTI</div>
      <div class="brand__rule"></div>
      <div class="brand__place">ITALY</div>
    </div>

    <div class="person">
      <div class="person__name">Dario Lorvanti</div>
      <div class="person__role">Position - CEO and CO Founder</div>
    </div>
    <div class="person-rule"></div>

    <ul class="contact contact--personal">
      <li><svg viewBox="0 0 24 24"><path d="M6.6 10.8a15 15 0 0 0 6.6 6.6l2.2-2.2a1 1 0 0 1 1-.25 11.4 11.4 0 0 0 3.6.57 1 1 0 0 1 1 1V20a1 1 0 0 1-1 1A17 17 0 0 1 3 4a1 1 0 0 1 1-1h3.5a1 1 0 0 1 1 1c0 1.25.2 2.45.57 3.57a1 1 0 0 1-.25 1z"/></svg>555-384-1926</li>
      <li><svg viewBox="0 0 24 24"><path d="M2 5h20v14H2zm2 2v.5l8 5 8-5V7l-8 5z"/></svg>dario@lorvanti.com</li>
    </ul>

    <ul class="contact contact--office">
      <li><svg viewBox="0 0 24 24"><path d="M6 2h10v6H6zM3 9h18v10h-3v3H6v-3H3zm5 7v4h8v-4z"/></svg>555-384-1926</li>
      <li><svg viewBox="0 0 24 24"><path d="M12 2a10 10 0 1 0 0 20 10 10 0 0 0 0-20zm6.9 9h-3a15 15 0 0 0-1.3-6 8 8 0 0 1 4.3 6zM12 4c.9 1.3 1.7 3.8 1.9 7h-3.8c.2-3.2 1-5.7 1.9-7zM9.4 5a15 15 0 0 0-1.3 6h-3a8 8 0 0 1 4.3-6zm-4.3 8h3a15 15 0 0 0 1.3 6 8 8 0 0 1-4.3-6zM12 20c-.9-1.3-1.7-3.8-1.9-7h3.8c-.2 3.2-1 5.7-1.9 7zm2.6-1a15 15 0 0 0 1.3-6h3a8 8 0 0 1-4.3 6z"/></svg>Lorvanti.com</li>
    </ul>

    <ul class="contact contact--address">
      <li><svg viewBox="0 0 24 24"><path d="M12 2a7 7 0 0 0-7 7c0 5 7 13 7 13s7-8 7-13a7 7 0 0 0-7-7zm0 9.5A2.5 2.5 0 1 1 12 6.5a2.5 2.5 0 0 1 0 5z"/></svg>4817 E Halvern</li>
    </ul>
  </section>

</main>
</body>
</html>
```